Create Stationary from existing logo(s)

We are looking for some assistance in tidying up the stationary that supports our brand. We are an innovative technology company, generally working with larger corporates. We have previously done a little work on brochures etc, but never really pulled it all together with our stationary.
In particular I am looking for:
1. A4 Letter Template for Letter (Microsoft Word 2007 template format)
2. A4 Template for Reports (Microsoft Word 2007 template format). This should include title page, table of contents, subsequent report pages including styles for tables, headings, and text.
3. Business Card Design - we will need to be able to edit the text, so the card should include sample text for name, title, phone number, mobile number, and email address.
4. Presentation Template (Microsoft Powerpoint 2007 template). See attached powerpoint which we quite like, but isn't really a template, and we have don't really use any consistent styles in it. The Powerpoint template needs to have a cover / title page, section break pages, and pages that may contain bullet point text, pictures, or a combination of bullet point text and pictures. We do like our current presentation, which gives some indication of our thinking.
I am attaching a brochure and the powerpoint presentation to give some indication of current materials. We are happy with the main concepts behind the brochure, and would not really be looking to change the key concepts unless you have a compelling reason. We do like the use of this secondary logo in the stationary related items
I have uploaded an eps file of the logo.

```html
<!DOCTYPE html>
<html lang="en">
<head>
<meta charset="utf-8">
<title>Vectra Systems — Business Card</title>
<link rel="stylesheet" href="https://fonts.googleapis.com/css2?family=Cinzel:wght@400&family=Tinos:wght@400;700&display=swap">
<style>
  :root {
    --page-bg: #e9e9e7;
    --card-blue: #1f4d84;
    --card-white: #ffffff;
    --brand-orange: #f29423;
    --brand-blue: #1d4f8c;
    --ink: #3a3a3a;
    --ink-soft: #5a5a5a;
    --shadow: rgba(0, 0, 0, 0.18);
  }
  * { box-sizing: border-box; margin: 0; padding: 0; }
  html, body { width: 1200px; height: 900px; overflow: hidden; }
  body {
    background: var(--page-bg);
    position: relative;
    font-family: "Tinos", "Times New Roman", serif;
  }
  .card {
    position: absolute;
    top: 285px;
    width: 540px;
    height: 330px;
    border-radius: 30px;
    box-shadow: 0 6px 18px var(--shadow);
    overflow: hidden;
  }
  .card--front { left: 45px; background: var(--card-blue); }
  .card--back { left: 615px; background: var(--card-white); }

  .front-wordmark {
    position: absolute;
    left: 40px;
    top: 30px;
    font-family: "Cinzel", "Times New Roman", serif;
    font-weight: 400;
    font-size: 96px;
    line-height: 98px;
    letter-spacing: 10px;
    color: var(--card-white);
  }
  .front-rule {
    position: absolute;
    left: 30px;
    right: 30px;
    top: 250px;
    height: 1px;
    background: rgba(255, 255, 255, 0.45);
  }
  .front-tagline {
    position: absolute;
    left: 40px;
    bottom: 36px;
    font-size: 15px;
    color: var(--brand-orange);
    letter-spacing: 0.5px;
  }
  .front-motto {
    position: absolute;
    right: 40px;
    top: 228px;
    font-size: 12px;
    color: rgba(255, 255, 255, 0.85);
  }

  .brand {
    position: absolute;
    top: 34px;
    right: 38px;
    display: flex;
    align-items: center;
    gap: 8px;
  }
  .brand__dot {
    width: 14px;
    height: 14px;
    border-radius: 50%;
    background: var(--brand-orange);
  }
  .brand__name {
    font-weight: 700;
    font-size: 20px;
    color: var(--brand-blue);
  }

  .contact {
    position: absolute;
    left: 40px;
    top: 130px;
    color: var(--ink);
  }
  .contact__name { font-size: 19px; line-height: 22px; }
  .contact__title {
    font-size: 9px;
    letter-spacing: 0.8px;
    text-transform: uppercase;
    color: var(--ink-soft);
    margin-bottom: 12px;
  }
  .contact__lines { font-size: 12.5px; line-height: 17px; }
  .contact__web { margin-top: 12px; font-size: 12.5px; line-height: 17px; }
</style>
</head>
<body>
  <section class="card card--front" aria-label="Business card front">
    <div class="front-wordmark">VEC<br>TRA</div>
    <div class="front-rule"></div>
    <p class="front-motto">Delivering Success</p>
    <p class="front-tagline">Skilled Information Technology Partners</p>
  </section>

  <section class="card card--back" aria-label="Business card back">
    <div class="brand">
      <span class="brand__dot"></span>
      <span class="brand__name">Vectra Systems</span>
    </div>
    <div class="contact">
      <p class="contact__name">Lena Marsh</p>
      <p class="contact__title">Account Manager</p>
      <p class="contact__lines">
        Level 4, 120 Harbour Street<br>
        Sydney 2000 Australia<br>
        Phone: +61 2 5550 3170<br>
        Fax: +61 2 5550 8264<br>
        Mobile: +61 2 5550 8264
      </p>
      <p class="contact__web">
        lena.marsh@vectrasystems.com.au<br>
        www.vectrasystems.com.au
      </p>
    </div>
  </section>
</body>
</html>
```